Builder of high-end, expensive tables and other furniture

Build a website that represents what we do. I want a luxury feel that appeals to those who can afford our products. We build very high end tables and other furniture using trees that have fallen or are standing dead. We never cut living trees. Trees are harvested, milled, and kiln dried. Then that lumber is meticulously turned into fine furniture using the best equipment. Our furniture prices range from $1,000-$20,000.

Trying to figure out how to raise my spend.

```html
<!DOCTYPE html>
<html lang="en">
<head>
<meta charset="utf-8">
<title>Fallen Oak Tables — Fine Furniture from Fallen Trees</title>
<link href="https://fonts.googleapis.com/css2?family=Raleway:wght@500;600;700&family=Roboto:wght@400;500;700&display=swap" rel="stylesheet">
<style>
:root{
  --orange:#ee7a35;
  --orange-deep:#e5702a;
  --blue:#4aa8e6;
  --footer-blue:#3a85c9;
  --ink:#333;
  --muted:#666;
  --pale-blue:#eef3f7;
  --cream:#f8f4ef;
  --white:#fff;
}
*{box-sizing:border-box;margin:0;padding:0}
html,body{width:1200px;height:4148px;overflow:hidden}
body{position:relative;background:var(--white);font-family:'Roboto',sans-serif;color:var(--ink)}
.abs{position:absolute}
.head-font{font-family:'Raleway',sans-serif}

/* header */
.site-header{position:absolute;left:0;top:0;width:1200px;height:145px;background:var(--white)}
.brand{left:111px;top:50px;display:flex;align-items:center;gap:10px;font-family:'Roboto',sans-serif;font-size:34px;font-weight:500;color:var(--orange)}
.brand-dot{width:22px;height:22px;border-radius:50%;background:var(--orange)}
.search{left:762px;top:27px;width:325px;height:39px;border:1px solid #ccc;display:flex;align-items:center;padding-left:8px;gap:14px;font-size:13px;color:#444}
.search-btn{width:28px;height:28px;border-radius:50%;background:var(--blue);display:flex;align-items:center;justify-content:center}
.nav{top:96px;font-size:12px;font-weight:500;color:#222;text-transform:uppercase}
.nav.active{color:var(--blue)}
.round-icon{width:30px;height:30px;border-radius:50%;background:var(--orange);display:flex;align-items:center;justify-content:center;top:89px}

/* hero */
.hero{left:0;top:145px;width:1200px;height:617px;background:linear-gradient(100deg,#5a3520 0%,#8a5a36 30%,#6b6258 55%,#3c3f44 80%,#2f3236 100%)}
.hero-kicker{left:111px;top:324px;color:#fff;font-family:'Raleway',sans-serif;font-size:21px;font-weight:500}
.hero-title{left:111px;top:352px;color:#fff;font-family:'Raleway',sans-serif;font-size:42px;font-weight:600}
.hero-text{left:111px;top:418px;width:400px;color:#fff;font-size:19px;font-weight:500;line-height:29px}
.btn{display:flex;align-items:center;justify-content:center;background:var(--orange);color:#fff;font-size:13px;font-weight:500;text-transform:uppercase}

/* what we do */
.wwd-photo-frame{left:111px;top:915px;width:562px;height:428px;background:#fff;box-shadow:0 2px 8px rgba(0,0,0,.15)}
.wwd-photo{left:118px;top:921px;width:549px;height:416px;background:linear-gradient(90deg,#3d3d3d 0%,#6f6a66 45%,#9a6a3e 75%,#2a2a2a 100%)}
.wwd-card{left:530px;top:1044px;width:557px;height:415px;background:#fff;box-shadow:0 2px 14px rgba(0,0,0,.1)}
.section-title{font-family:'Raleway',sans-serif;font-weight:600;font-size:38px;color:var(--orange);text-transform:uppercase}
.section-title span{color:var(--blue)}
.wwd-text{left:581px;top:1165px;width:456px;font-size:14px;line-height:26px;color:var(--muted);text-align:justify}

/* products */
.products{left:0;top:1595px;width:1200px;height:546px;background:var(--pale-blue)}
.product-card{top:1756px;width:227px;height:238px;background:#fff;box-shadow:0 1px 4px rgba(0,0,0,.06)}
.product-name{top:2017px;width:227px;text-align:center;font-size:17px;color:#222}
.product-price{top:2050px;width:227px;text-align:center;font-size:15px;color:var(--orange);font-weight:500}

/* how it works */
.how{left:0;top:2141px;width:1200px;height:470px;background:var(--orange-deep)}
.how-title{top:2208px;width:1200px;text-align:center;color:#fff;font-family:'Raleway',sans-serif;font-weight:600;font-size:35px}
.step-icon{width:102px;height:102px;border-radius:50%;background:var(--blue);border:5px solid #fff;display:flex;align-items:center;justify-content:center;top:2285px}
.step-title{top:2421px;width:340px;text-align:center;color:#fff;font-size:19px;font-weight:500}
.step-text{top:2462px;width:300px;text-align:center;color:#fff;font-size:14px;line-height:24px;opacity:.95}

/* blog */
.blog-photo{top:2816px;width:311px;height:214px}
.blog-box{top:2998px;width:283px;height:195px;background:#fff;box-shadow:0 1px 6px rgba(0,0,0,.08);text-align:center}
.blog-date{margin-top:22px;font-size:12px;color:#888}
.blog-date b{color:var(--orange);font-weight:400}
.blog-title{margin-top:12px;font-size:16px;line-height:25px;color:var(--blue);text-transform:uppercase;padding:0 14px}
.blog-text{margin-top:6px;font-size:14.5px;line-height:23px;color:var(--muted);padding:0 18px}

/* testimonials */
.testimonials{left:0;top:3322px;width:1200px;height:522px;background:var(--cream)}
.test-card{top:3470px;width:309px;height:300px;background:#fff;border-radius:8px;text-align:center}
.avatar{position:absolute;left:114px;top:23px;width:80px;height:80px;border-radius:50%;background:#c9b6a3;border:3px solid #e2e2e2}
.quote-mark{position:absolute;font-family:'Raleway',sans-serif;font-size:80px;color:#ddd;line-height:1}
.test-text{position:absolute;left:24px;top:118px;width:261px;font-size:14.5px;line-height:27px;color:#555}
.test-name{position:absolute;top:235px;width:100%;font-size:16px;color:var(--blue);font-weight:500}
.stars{position:absolute;top:262px;width:100%;font-size:11px;letter-spacing:2px;color:var(--orange)}
.arrow-btn{width:36px;height:36px;border-radius:50%;background:#fff;display:flex;align-items:center;justify-content:center;box-shadow:0 1px 4px rgba(0,0,0,.1);top:3602px}

/* footer */
.site-footer{left:0;top:3844px;width:1200px;height:304px;background:var(--footer-blue);color:#fff}
.foot-head{top:3903px;font-size:20px;font-weight:500;text-transform:uppercase}
.foot-link{font-size:15px}
.email-field{left:596px;top:3957px;width:298px;height:40px;border-bottom:1px solid rgba(255,255,255,.7);font-size:13px;padding-top:12px}
.contact-row{left:596px;top:4028px;font-size:13px;display:flex;align-items:center;gap:14px}
.social{width:12px;height:12px;border-radius:50%;background:#fff;display:inline-block}
.divider{left:111px;top:4100px;width:978px;height:1px;background:rgba(255,255,255,.6)}
.copyright{top:4117px;width:1200px;text-align:center;font-size:12px}
</style>
</head>
<body>

<header class="site-header">
  <div class="abs brand"><span class="brand-dot"></span>Fallen Oak Tables</div>
  <div class="abs search">
    <span class="search-btn"><svg width="14" height="14" viewBox="0 0 14 14"><circle cx="6" cy="6" r="4" fill="none" stroke="#fff" stroke-width="2"/><line x1="9" y1="9" x2="12.5" y2="12.5" stroke="#fff" stroke-width="2"/></svg></span>
    Search Products...
  </div>
  <span class="abs nav active" style="left:477px">Home</span>
  <span class="abs nav" style="left:538px">About Us</span>
  <span class="abs nav" style="left:625px">Products</span>
  <span class="abs nav" style="left:717px">Blog</span>
  <span class="abs nav" style="left:775px">Contact Us</span>
  <span class="abs round-icon" style="left:890px"><svg width="14" height="14" viewBox="0 0 14 14"><circle cx="7" cy="4.5" r="3" fill="#fff"/><path d="M1.5 13c0-3 2.5-5 5.5-5s5.5 2 5.5 5z" fill="#fff"/></svg></span>
  <span class="abs nav" style="left:936px;top:94px;text-decoration:underline">Login</span>
  <span class="abs round-icon" style="left:1006px"><svg width="14" height="14" viewBox="0 0 14 14"><rect x="2" y="5" width="10" height="8" rx="1" fill="#fff"/><path d="M4.5 5V3.5a2.5 2.5 0 0 1 5 0V5" fill="none" stroke="#fff" stroke-width="1.5"/></svg></span>
  <span class="abs nav" style="left:1054px">$0.00</span>
</header>

<section>
  <div class="abs hero" role="img" aria-label="Photo of a modern kitchen with a live-edge walnut counter and bar stools"></div>
  <div class="abs hero-kicker">WELCOME TO</div>
  <h1 class="abs hero-title">FALLEN OAK TABLES</h1>
  <p class="abs hero-text">We build very high end tables and other furniture using trees that have fallen or are standing dead.</p>
  <a class="abs btn" style="left:111px;top:536px;width:135px;height:42px">Learn More</a>
</section>

<section>
  <svg class="abs" style="left:495px;top:1008px" width="566" height="402" viewBox="0 0 566 402">
    <polyline points="172,4 560,4 560,36" fill="none" stroke="var(--blue)" stroke-width="2"/>
    <polyline points="4,329 4,398 36,398" fill="none" stroke="var(--blue)" stroke-width="2"/>
  </svg>
  <div class="abs wwd-photo-frame"></div>
  <div class="abs wwd-photo" role="img" aria-label="Photo of a bathroom with a timber vanity, black mirror and pendant lamp"></div>
  <div class="abs wwd-card"></div>
  <h2 class="abs section-title" style="left:581px;top:1090px">What <span>We Do</span></h2>
  <p class="abs wwd-text">Lorem ipsum dolor sit amet, consectetur adipiscing elit, sed do eiusmod tempor incididunt ut labore et dolore magna aliqua. Ut enim ad minim veniam, quis nostrud exercitation ullamco laboris nisi ut aliquip ex ea commodo consequat. Duis aute irure dolor in reprehenderit in voluptate velit esse cillum dolore eu fugiat nulla pariatur. Excepteur sint occaecat cupidatat non proident.</p>
  <a class="abs btn" style="left:581px;top:1355px;width:137px;height:46px">Learn More</a>
</section>

<section>
  <div class="abs products"></div>
  <h2 class="abs section-title" style="left:0;top:1659px;width:1200px;text-align:center">Our <span>Products</span></h2>

  <div class="abs product-card" style="left:111px"><div role="img" aria-label="Photo of an oak chest of drawers" style="margin:55px auto 0;width:110px;height:150px;background:linear-gradient(180deg,#d9995a,#b86e35)"></div></div>
  <div class="abs product-name" style="left:111px">Lorem ipsum dolor</div>
  <div class="abs product-price" style="left:111px">$15,000</div>

  <div class="abs product-card" style="left:361px"><div role="img" aria-label="Photo of a dark walnut dresser" style="margin:62px auto 0;width:130px;height:120px;background:linear-gradient(180deg,#6a5444,#45352a)"></div></div>
  <div class="abs product-name" style="left:361px">Lorem ipsum dolor</div>
  <div class="abs product-price" style="left:361px">$15,000</div>

  <div class="abs product-card" style="left:611px"><div role="img" aria-label="Photo of a teal chair with wooden legs" style="margin:48px auto 0;width:100px;height:148px;background:linear-gradient(180deg,#4e9b8a 0%,#4e9b8a 45%,#d89a4c 55%,#c98638 100%)"></div></div>
  <div class="abs product-name" style="left:611px">Lorem ipsum dolor</div>
  <div class="abs product-price" style="left:611px">$15,000</div>

  <div class="abs product-card" style="left:861px"><div role="img" aria-label="Photo of a round pedestal side table" style="margin:48px auto 0;width:115px;height:150px;background:linear-gradient(180deg,#7a4a22,#a8682f)"></div></div>
  <div class="abs product-name" style="left:861px">Lorem ipsum dolor</div>
  <div class="abs product-price" style="left:861px">$15,000</div>
</section>

<section>
  <div class="abs how" role="img" aria-label="Faded photo of a wood workshop under an orange overlay"></div>
  <h2 class="abs how-title">HOW IT WORKS</h2>

  <div class="abs step-icon" style="left:207px"><svg width="50" height="50" viewBox="0 0 50 50" fill="none" stroke="#fff" stroke-width="2"><line x1="25" y1="8" x2="25" y2="44"/><line x1="15" y1="14" x2="15" y2="40"/><line x1="35" y1="14" x2="35" y2="40"/><path d="M25 16l-5-4M25 24l-5-4M25 32l-5-4M25 16l5-4M25 24l5-4M25 32l5-4"/></svg></div>
  <h3 class="abs step-title" style="left:88px">HARVESTED</h3>
  <p class="abs step-text" style="left:108px">Sed ut perspiciatis unde omnis iste natus error sit voluptatem accusantium doloremque laudantium, totam rem aperiam, eaque ipsa.</p>

  <div class="abs step-icon" style="left:548px"><svg width="50" height="50" viewBox="0 0 50 50" fill="none" stroke="#fff" stroke-width="2"><circle cx="22" cy="26" r="8"/><circle cx="22" cy="26" r="14" stroke-dasharray="5 4"/><path d="M34 10h10v10"/></svg></div>
  <h3 class="abs step-title" style="left:429px">MILLED</h3>
  <p class="abs step-text" style="left:449px">Sed ut perspiciatis unde omnis iste natus error sit voluptatem accusantium doloremque laudantium, totam rem aperiam, eaque ipsa.</p>

  <div class="abs step-icon" style="left:890px"><svg width="50" height="50" viewBox="0 0 50 50" fill="none" stroke="#fff" stroke-width="2"><rect x="8" y="8" width="34" height="34" rx="2"/><rect x="14" y="16" width="22" height="20"/><path d="M25 32c-4 0-5-4-2-8 1 3 3 2 3 0 3 3 3 8-1 8z"/></svg></div>
  <h3 class="abs step-title" style="left:771px">KILN DRIED</h3>
  <p class="abs step-text" style="left:791px">Sed ut perspiciatis unde omnis iste natus error sit voluptatem accusantium doloremque laudantium, totam rem aperiam, eaque ipsa.</p>
</section>

<section>
  <h2 class="abs section-title" style="left:0;top:2724px;width:1200px;text-align:center">Latest <span>Blog Post</span></h2>

  <div class="abs blog-photo" style="left:111px;background:linear-gradient(160deg,#b98d63,#e6c6a0 50%,#8b6444)" role="img" aria-label="Photo of a live-edge table top"></div>
  <article class="abs blog-box" style="left:125px">
    <p class="blog-date"><b>▦</b>&nbsp; 22 MAY 2023</p>
    <h3 class="blog-title">Lorem ipsum dolor sit amet, consea</h3>
    <p class="blog-text">Lorem ipsum dolor sit amet, conse cte tur adipiscing elit, sed do eiusmod tempor.</p>
  </article>

  <div class="abs blog-photo" style="left:445px;background:linear-gradient(160deg,#5a3b25,#c9a584 50%,#e9e2d6)" role="img" aria-label="Photo of a timber-beamed living room"></div>
  <article class="abs blog-box" style="left:459px">
    <p class="blog-date"><b>▦</b>&nbsp; 22 MAY 2023</p>
    <h3 class="blog-title">Lorem ipsum dolor sit amet, consea</h3>
    <p class="blog-text">Lorem ipsum dolor sit amet, conse cte tur adipiscing elit, sed do eiusmod tempor.</p>
  </article>

  <div class="abs blog-photo" style="left:778px;background:linear-gradient(160deg,#c98a2c,#e8b35a 50%,#7a4f1c)" role="img" aria-label="Photo of a burl wood table edge"></div>
  <article class="abs blog-box" style="left:792px">
    <p class="blog-date"><b>▦</b>&nbsp; 22 MAY 2023</p>
    <h3 class="blog-title">Lorem ipsum dolor sit amet, consea</h3>
    <p class="blog-text">Lorem ipsum dolor sit amet, conse cte tur adipiscing elit, sed do eiusmod tempor.</p>
  </article>
</section>

<section>
  <div class="abs testimonials"></div>
  <h2 class="abs section-title" style="left:0;top:3384px;width:1200px;text-align:center">Testimonials</h2>

  <span class="abs arrow-btn" style="left:37px"><svg width="10" height="10" viewBox="0 0 10 10"><path d="M7 1L3 5l4 4" fill="none" stroke="#222" stroke-width="1.8"/></svg></span>
  <span class="abs arrow-btn" style="left:1127px"><svg width="10" height="10" viewBox="0 0 10 10"><path d="M3 1l4 4-4 4" fill="none" stroke="#222" stroke-width="1.8"/></svg></span>

  <figure class="abs test-card" style="left:111px">
    <div class="avatar" role="img" aria-label="Customer portrait"></div>
    <span class="quote-mark" style="left:18px;top:108px">“</span>
    <p class="test-text">Lorem ipsum dolor sit amet, consec tetur adipiscing elit, sed do eiusmod tempor incididunt ut labore et dolore magna aliqua.</p>
    <span class="quote-mark" style="right:18px;top:180px">”</span>
    <figcaption class="test-name">- Nora Bell</figcaption>
    <div class="stars">★★★★★</div>
  </figure>

  <figure class="abs test-card" style="left:446px">
    <div class="avatar" role="img" aria-label="Customer portrait"></div>
    <span class="quote-mark" style="left:18px;top:108px">“</span>
    <p class="test-text">Lorem ipsum dolor sit amet, consec tetur adipiscing elit, sed do eiusmod tempor incididunt ut labore et dolore magna aliqua.</p>
    <span class="quote-mark" style="right:18px;top:180px">”</span>
    <figcaption class="test-name">- Owen Price</figcaption>
    <div class="stars">★★★★★</div>
  </figure>

  <figure class="abs test-card" style="left:780px">
    <div class="avatar" role="img" aria-label="Customer portrait"></div>
    <span class="quote-mark" style="left:18px;top:108px">“</span>
    <p class="test-text">Lorem ipsum dolor sit amet, consec tetur adipiscing elit, sed do eiusmod tempor incididunt ut labore et dolore magna aliqua.</p>
    <span class="quote-mark" style="right:18px;top:180px">”</span>
    <figcaption class="test-name">- Leo Grant</figcaption>
    <div class="stars">★★★★★</div>
  </figure>
</section>

<footer>
  <div class="abs site-footer"></div>
  <h4 class="abs foot-head" style="left:111px;color:#fff">Quick Links</h4>
  <a class="abs foot-link" style="left:111px;top:3958px;color:#fff">Home</a>
  <a class="abs foot-link" style="left:111px;top:3993px;color:#fff">About</a>
  <a class="abs foot-link" style="left:111px;top:4027px;color:#fff">Products</a>
  <a class="abs foot-link" style="left:111px;top:4062px;color:#fff">Blog</a>
  <a class="abs foot-link" style="left:333px;top:3958px;color:#fff">Privacy Policy</a>
  <a class="abs foot-link" style="left:333px;top:3993px;color:#fff">Terms Of Use</a>
  <a class="abs foot-link" style="left:333px;top:4027px;color:#fff">Contact Us</a>

  <h4 class="abs foot-head" style="left:596px;color:#fff">Join Our Newsletter</h4>
  <div class="abs email-field" style="color:#fff">Enter Your Email Here</div>
  <a class="abs btn" style="left:933px;top:3947px;width:133px;height:51px;font-size:14px;font-weight:700">Subscribe</a>

  <div class="abs contact-row" style="color:#fff">
    <span><svg width="10" height="10" viewBox="0 0 10 10"><path d="M2 1l2 2-1 1.5c.8 1.4 1.6 2.2 3 3L7.5 6l2 2-1.5 1.5C4.5 9 1 5.5.5 2.5z" fill="#fff"/></svg>&nbsp; +1 (555) 010 0100</span>
    <span>|</span>
    <span><svg width="12" height="9" viewBox="0 0 12 9"><rect width="12" height="9" fill="#fff"/><path d="M0 0l6 5 6-5" fill="none" stroke="var(--footer-blue)" stroke-width="1"/></svg>&nbsp; info@fallenoaktables.com</span>
    <span>|</span>
    <span class="social"></span><span class="social"></span><span class="social"></span><span class="social"></span>
  </div>

  <div class="abs divider"></div>
  <p class="abs copyright" style="color:#fff">© 2023 FALLEN OAK TABLES &nbsp;|&nbsp; All Rights Reserved</p>
</footer>

</body>
</html>
```